HotSite for a 3-day Conference (To build in 24hs)

We need a hot-site for our 3-Day Conference before next Wednesday 17/Jan.

How is it now:
Today all information about our conference is shown in 1 simple page inside our website: https://www.kelvortaplin.com/grand-lodging-forum.

What we need:
A hot-site focused on our conference where people can see all information about the event, buy tickets and pay it on-line.

The visual:
Luxury, minimalist menu, big full screen light video backgrounds.

Index:
Full animated/light video image and:
Grand Lodging Forum® Paris - 2024
1, 2 and 3rd November
Hotel Le Moulin Doré
REGISTER NOW

MENU
I want a double layer/line top menu:

- First menu line (smaller, not the most important/relevant)
- Second menu line (main menu)

First menu line:
About us
Conferences
Newsroom
Careers
Become a Sponsor

The main menu items are:
AGENDA
SPEAKERS
SPONSORS
PREVIOUS EDITIONS
ATTEND/REGISTER NOW

Some references:
https://primeworld.live.qz.com
https://brevand.us/conference
https://www.holtrane.com/en/conferences

```html
<!DOCTYPE html>
<html lang="en">
<head>
<meta charset="utf-8">
<title>Grand Lodging Forum® Paris 2024</title>
<link href="https://fonts.googleapis.com/css2?family=Great+Vibes&family=Roboto+Condensed:ital,wght@0,400;0,700;1,400;1,700&family=Roboto:wght@400;500&display=swap" rel="stylesheet">
<style>
:root{
  --gold:#d2b06a;
  --gold-deep:#c48f2c;
  --panel:rgba(22,22,22,.93);
  --panel-low:rgba(22,22,22,.72);
  --white:#ffffff;
  --ink:#222222;
  --card-grey:rgba(205,205,205,.88);
  --btn:#d9a640;
}
*{box-sizing:border-box;margin:0;padding:0}
html,body{width:1200px;height:3457px;overflow:hidden}
body{font-family:"Roboto Condensed",sans-serif;color:var(--white);position:relative}
.backdrop{position:absolute;inset:0;background:linear-gradient(180deg,#4a5f7f 0%,#6c7e96 20%,#7e8894 38%,#5d6560 55%,#3f4a37 75%,#2e3a26 100%)}
.panel{position:absolute;left:111px;top:0;width:977px;height:3457px;background:linear-gradient(180deg,var(--panel) 0%,var(--panel) 35%,var(--panel-low) 60%,rgba(22,22,22,.6) 100%)}
.abs{position:absolute}
.center{text-align:center;left:111px;width:977px}
.brand{font-family:"Roboto Condensed",sans-serif;font-weight:400;color:var(--gold);font-size:30px;letter-spacing:1px;white-space:nowrap;transform:translateX(-50%)}
.topnav a,.mainnav a,.footnav a{position:absolute;color:var(--white);text-decoration:none;font-family:"Roboto",sans-serif;font-size:15px;white-space:nowrap;transform:translateX(-50%)}
.mainnav a{font-size:14.5px}
.btn-register{position:absolute;left:934px;top:64px;width:110px;height:34px;border-radius:17px;background:var(--btn);color:var(--white);font-family:"Roboto",sans-serif;font-size:14px;display:flex;align-items:center;justify-content:center;text-decoration:none}
.play{position:absolute;left:572px;top:193px;width:54px;height:54px;border-radius:50%;background:radial-gradient(circle,#6a5318 0%,#4a3a12 60%,rgba(90,70,20,0) 100%);box-shadow:0 0 22px 8px rgba(160,120,30,.35)}
.script{font-family:"Great Vibes",cursive;color:var(--gold);font-weight:400}
.hero-title{font-size:44px}
.hero-city{font-style:italic;font-weight:700;color:var(--gold);font-size:30px}
.hero-date{font-style:italic;font-weight:700;color:var(--gold);font-size:32px}
.intro{font-size:14.5px;line-height:26px}
.section-head{font-style:italic;font-weight:700;color:var(--gold);font-size:20px}
.topic{font-size:15px;display:flex;align-items:center;gap:7px;white-space:nowrap}
.tick{width:30px;height:30px;flex:none}
.price-card{position:absolute;width:228px;height:151px;border-radius:14px;background:var(--card-grey);text-align:center;font-style:italic;font-weight:700;color:var(--ink);font-size:20px;line-height:29px;padding-top:30px}
.price-card .amount{color:var(--white)}
.address{font-size:11px;color:var(--gold);line-height:19px}
.section-title{font-size:40px}
.speaker{position:absolute;width:240px;text-align:center;transform:translateX(-50%)}
.speaker .photo{width:152px;height:152px;border-radius:50%;margin:0 auto;background:radial-gradient(circle at 50% 35%,#6b5a4c 0%,#2e2a2a 55%,#1a1c22 100%)}
.speaker .photo.leafy{background:radial-gradient(circle at 50% 40%,#5c6a56 0%,#3b5532 55%,#24361f 100%)}
.speaker .photo.red{background:radial-gradient(circle at 50% 40%,#3a3a48 0%,#7a1c1c 65%,#4a1010 100%)}
.speaker .photo.warm{background:radial-gradient(circle at 50% 40%,#b08870 0%,#6b5040 60%,#3e2e26 100%)}
.speaker .name{color:var(--gold);font-size:21px;margin-top:10px}
.speaker .role{font-family:"Great Vibes",cursive;color:var(--gold);font-size:16px;line-height:26px}
.day-card{position:absolute;width:393px;height:499px;background:var(--white);border-radius:12px;color:var(--ink);padding:22px 0 0 11px}
.day-card h3{color:var(--gold-deep);font-weight:700;font-size:20px;margin-bottom:6px}
.day-card ul{list-style:none;padding-left:4px;font-size:14.5px}
.day-card.compact li{line-height:27.5px}
.day-card.mid li{line-height:34px}
.day-card.wide li{line-height:37.6px}
.footnav a{font-size:16px}
.copyright{font-family:"Roboto",sans-serif;font-size:12px}
</style>
</head>
<body>
<div class="backdrop" role="img" aria-label="Aerial photo of Paris at dusk with the Eiffel Tower and tree-lined avenues"></div>
<div class="panel"></div>

<header>
  <nav class="topnav">
    <a href="#" style="left:165px;top:72px">About us</a>
    <a href="#" style="left:288px;top:72px">Conferences</a>
    <a href="#" style="left:418px;top:72px">Newsroom</a>
    <a href="#" style="left:708px;top:72px">Careers</a>
    <a href="#" style="left:848px;top:72px">Become a Sponsor</a>
  </nav>
  <div class="abs brand" style="left:600px;top:60px">Kelvor Taplin</div>
  <a class="btn-register" href="#">Register Now</a>
  <nav class="mainnav">
    <a href="#" style="left:346px;top:159px">Agenda</a>
    <a href="#" style="left:459px;top:159px">Speakers</a>
    <a href="#" style="left:577px;top:159px">Sponsors</a>
    <a href="#" style="left:722px;top:159px">Previous Editions</a>
    <a href="#" style="left:857px;top:159px">Attend</a>
  </nav>
</header>

<main>
  <div class="play">
    <svg width="54" height="54" viewBox="0 0 54 54"><path d="M22 18 L36 27 L22 36 Z" fill="#ffffff"/></svg>
  </div>
  <h1 class="abs center script hero-title" style="top:246px">Grand Lodging Forum®</h1>
  <div class="abs center hero-city" style="top:307px">Paris</div>
  <div class="abs center hero-date" style="top:355px">November 1-3, 2024</div>
  <div class="abs center intro" style="top:421px">
    <p>The ever-growing Luxury Hospitality business is one of the most exciting industries in the world.</p>
    <p style="margin-top:20px">At our Grand Lodging Forum, top figures in the industry share their experiences and give unique<br>insights, speaking about challenges, entrepreneurial management, vision and prospects for the future.</p>
    <p style="margin-top:18px">The forum leads directly into HôtelExpo, the most important Hospitality event in the world.</p>
  </div>

  <h2 class="abs section-head" style="left:164px;top:620px">Content</h2>
  <ul class="topics" style="list-style:none">
    <li class="abs topic" style="left:164px;top:663px"><svg class="tick" viewBox="0 0 30 30"><circle cx="15" cy="15" r="11" fill="none" stroke="#ffffff" stroke-width="1" stroke-dasharray="2 3"/><path d="M9 15 L13 19 L21 10" fill="none" stroke="var(--gold)" stroke-width="1.6"/></svg>The Luxury Traveller's Evolution Over Time</li>
    <li class="abs topic" style="left:164px;top:707px"><svg class="tick" viewBox="0 0 30 30"><circle cx="15" cy="15" r="11" fill="none" stroke="#ffffff" stroke-width="1" stroke-dasharray="2 3"/><path d="M9 15 L13 19 L21 10" fill="none" stroke="var(--gold)" stroke-width="1.6"/></svg>Luxury Consumer Behavior</li>
    <li class="abs topic" style="left:164px;top:751px"><svg class="tick" viewBox="0 0 30 30"><circle cx="15" cy="15" r="11" fill="none" stroke="#ffffff" stroke-width="1" stroke-dasharray="2 3"/><path d="M9 15 L13 19 L21 10" fill="none" stroke="var(--gold)" stroke-width="1.6"/></svg>New Distribution Channels in Luxury Hospitality</li>
    <li class="abs topic" style="left:164px;top:796px"><svg class="tick" viewBox="0 0 30 30"><circle cx="15" cy="15" r="11" fill="none" stroke="#ffffff" stroke-width="1" stroke-dasharray="2 3"/><path d="M9 15 L13 19 L21 10" fill="none" stroke="var(--gold)" stroke-width="1.6"/></svg>Luxury Brand Management</li>
    <li class="abs topic" style="left:164px;top:840px"><svg class="tick" viewBox="0 0 30 30"><circle cx="15" cy="15" r="11" fill="none" stroke="#ffffff" stroke-width="1" stroke-dasharray="2 3"/><path d="M9 15 L13 19 L21 10" fill="none" stroke="var(--gold)" stroke-width="1.6"/></svg>Innovation in Luxury Hospitality</li>
    <li class="abs topic" style="left:164px;top:884px"><svg class="tick" viewBox="0 0 30 30"><circle cx="15" cy="15" r="11" fill="none" stroke="#ffffff" stroke-width="1" stroke-dasharray="2 3"/><path d="M9 15 L13 19 L21 10" fill="none" stroke="var(--gold)" stroke-width="1.6"/></svg>Luxury Boutique Hotel Strategies</li>
    <li class="abs topic" style="left:164px;top:928px"><svg class="tick" viewBox="0 0 30 30"><circle cx="15" cy="15" r="11" fill="none" stroke="#ffffff" stroke-width="1" stroke-dasharray="2 3"/><path d="M9 15 L13 19 L21 10" fill="none" stroke="var(--gold)" stroke-width="1.6"/></svg>How to Maintain Luxury in Large Scale Operations</li>
    <li class="abs topic" style="left:164px;top:971px"><svg class="tick" viewBox="0 0 30 30"><circle cx="15" cy="15" r="11" fill="none" stroke="#ffffff" stroke-width="1" stroke-dasharray="2 3"/><path d="M9 15 L13 19 L21 10" fill="none" stroke="var(--gold)" stroke-width="1.6"/></svg>Generating Unique Experiences</li>
    <li class="abs topic" style="left:164px;top:1018px"><svg class="tick" viewBox="0 0 30 30"><circle cx="15" cy="15" r="11" fill="none" stroke="#ffffff" stroke-width="1" stroke-dasharray="2 3"/><path d="M9 15 L13 19 L21 10" fill="none" stroke="var(--gold)" stroke-width="1.6"/></svg>Luxury Hotel Chain Management</li>
    <li class="abs topic" style="left:164px;top:1064px"><svg class="tick" viewBox="0 0 30 30"><circle cx="15" cy="15" r="11" fill="none" stroke="#ffffff" stroke-width="1" stroke-dasharray="2 3"/><path d="M9 15 L13 19 L21 10" fill="none" stroke="var(--gold)" stroke-width="1.6"/></svg>Forming Strategic Alliances</li>
  </ul>

  <h2 class="abs section-head" style="left:557px;top:619px">Tuition</h2>
  <div class="price-card" style="left:558px;top:658px">Early birds<br>until 08/30/2024<br><span class="amount">€3.750,00</span></div>
  <div class="price-card" style="left:824px;top:658px">After<br>08/30/2024<br><span class="amount">€5.000,00</span></div>
  <div class="price-card" style="left:558px;top:837px">KT Students<br>until 08/30/2024<br><span class="amount">€3.000,00</span></div>
  <div class="price-card" style="left:824px;top:837px">After<br>08/30/2024<br><span class="amount">€3.500,00</span></div>
  <div class="abs topic" style="left:556px;top:1016px"><svg class="tick" viewBox="0 0 30 30"><circle cx="15" cy="15" r="11" fill="none" stroke="#ffffff" stroke-width="1" stroke-dasharray="2 3"/><path d="M9 15 L13 19 L21 10" fill="none" stroke="var(--gold)" stroke-width="1.6"/></svg>Discounts available for groups and partner Universities</div>
  <div class="abs topic" style="left:556px;top:1061px"><svg class="tick" viewBox="0 0 30 30"><circle cx="15" cy="15" r="11" fill="none" stroke="#ffffff" stroke-width="1" stroke-dasharray="2 3"/><path d="M9 15 L13 19 L21 10" fill="none" stroke="var(--gold)" stroke-width="1.6"/></svg>Lodgind and meals not included</div>

  <address class="abs center address" style="top:1140px;font-style:normal">KELVOR TAPLIN EDUCATION LLC<br>1480 Orchard Park Ave ste 310 - San Jose, CA</address>

  <h2 class="abs center script section-title" style="top:1256px">Speaker Line-Up</h2>
  <section class="speakers">
    <div class="speaker" style="left:242px;top:1345px"><div class="photo" role="img" aria-label="Portrait of Renato Almeida"></div><div class="name">Renato Almeida</div><div class="role">President of Kelvor Taplin</div></div>
    <div class="speaker" style="left:483px;top:1345px"><div class="photo red" role="img" aria-label="Portrait of Jean-Marc Lavelle"></div><div class="name">Jean-Marc Lavelle</div><div class="role">CEO, La Verrière</div></div>
    <div class="speaker" style="left:728px;top:1345px"><div class="photo leafy" role="img" aria-label="Portrait of Pieter Vandam"></div><div class="name">Pieter Vandam</div><div class="role">CEO, Select Boutique Stays<br>of the World</div></div>
    <div class="speaker" style="left:968px;top:1345px"><div class="photo warm" role="img" aria-label="Portrait of Matthias Korver"></div><div class="name">Matthias Korver</div><div class="role">General Director, Hotel<br>Solenne Paris</div></div>
    <div class="speaker" style="left:350px;top:1615px"><div class="photo warm" role="img" aria-label="Portrait of Marco Dellari"></div><div class="name">Marco Dellari</div><div class="role">Former VP, Cedarline<br>Resorts</div></div>
    <div class="speaker" style="left:592px;top:1615px"><div class="photo red" role="img" aria-label="Portrait of Étienne Marchal"></div><div class="name">Étienne Marchal</div><div class="role">COO, Aldgate Collection</div></div>
    <div class="speaker" style="left:835px;top:1615px"><div class="photo leafy" role="img" aria-label="Portrait of Laurent Vermeulen"></div><div class="name">Laurent Vermeulen</div><div class="role">Former Executive VP, Maison Castel<br>(23 years)</div></div>
  </section>

  <h2 class="abs center script section-title" style="top:1921px">Daily Schedule</h2>
  <section class="day-card compact" style="left:164px;top:2041px">
    <h3>Nov. 1 - Tradition Vs. Innovation</h3>
    <ul>
      <li>09:00 - Official Opening</li>
      <li>Renato Almeida | Kelvor Taplin</li>
      <li>09:15 - The Legend Is Back</li>
      <li>Matthias Korver | Hôtel Solenne Paris</li>
      <li>10:30 - Coffee Break</li>
      <li>11:00 - The Luxury Traveller's Evolution Over Time</li>
      <li>Matthias Korver | Hôtel Solenne Paris</li>
      <li>12:00 - Lunch</li>
      <li>14:00 - Luxury Consumer Behavior</li>
      <li>Laurent Vermeulen | Maison Castel (23 years)</li>
      <li>15:30 - Coffee Break</li>
      <li>16:00 - Roads to Luxury</li>
      <li>Laurent Vermeulen | Maison Castel (23 years)</li>
      <li>17:00 - Closure</li>
      <li>19:30 - Social Program - Pâtisserie Class at École Varenne</li>
    </ul>
  </section>
  <section class="day-card mid" style="left:646px;top:2041px">
    <h3>Nov. 2 - The Era Of Experiences</h3>
    <ul>
      <li>09:00 - Luxury Boutique Hotel Strategies</li>
      <li>Jean-Marc Lavelle | La Verrière</li>
      <li>10:30 - Coffee Break</li>
      <li>11:00 - Generating Unique Experiences</li>
      <li>Jean-Marc Lavelle | La Verrière</li>
      <li>12:00 - Lunch</li>
      <li>14:00 - Smaller is Greater</li>
      <li>Pieter Vandam | Select Boutique Stays of the World</li>
      <li>15:30 - Coffee Break</li>
      <li>16:00 - Site Inspection - Spa Hotel La Verrière</li>
      <li>17:00 - Closure</li>
      <li>17:30 - Social Program - Guided Visit to Musée des Arts Royaux</li>
    </ul>
  </section>
  <section class="day-card wide" style="left:404px;top:2616px">
    <h3>Nov. 3 - A Glimpse Of The Future</h3>
    <ul>
      <li>09:00 - Innovation in Luxury Hospitality</li>
      <li>Marco Dellari | WorkNest</li>
      <li>10:30 - Coffee Break</li>
      <li>11:00 - Site Inspection - Hôtel Palais Montclair</li>
      <li>12:00 - Lunch</li>
      <li>14:00 - Luxury Hotel Chain Management</li>
      <li>Étienne Marchal | Aldgate Collection</li>
      <li>15:30 - Coffee Break</li>
      <li>16:00 - Panel of Discussion - New Competitors</li>
      <li>17:00 - Closure and Certificates</li>
    </ul>
  </section>
</main>

<footer>
  <div class="abs brand" style="left:600px;top:3244px">Kelvor Taplin</div>
  <nav class="footnav">
    <a href="#" style="left:334px;top:3345px">About us</a>
    <a href="#" style="left:488px;top:3345px">Conferences</a>
    <a href="#" style="left:649px;top:3345px">Newsroom</a>
    <a href="#" style="left:831px;top:3345px">Become a Sponsor</a>
  </nav>
  <div class="abs center copyright" style="top:3403px">© 2024 Kelvor Taplin Education | all Rights Reserved</div>
</footer>
</body>
</html>
```